QVN MOONLIT GLOW Party

Hi,
Want to design a flyer for a party.

I have attached a design I would like you to work from and just add in the correct text:

QVN Events presents

November 2013

MOONLIT GLOW
PARTY

DJ COPPER WHISK
VENUE: TBA

DOORS OPEN 8PM

ENTRY STRICTLY OVER 18'S.

DRESS CODE: SMART CASUAL SULTRY SEXY SPRING THREADS

COST: $60 PER HEAD, includes champagne, beer & wine and canapes.

Tickets from www.quillvanenest.example.com.au or 0499 371 582.

```html
<!DOCTYPE html>
<html lang="en">
<head>
<meta charset="utf-8">
<title>QVN Moonlit Glow Party Flyer</title>
<link rel="stylesheet" href="https://fonts.googleapis.com/css2?family=Montserrat:wght@500;700;800&family=Roboto+Condensed:wght@400&display=swap">
<style>
  :root {
    --ink: #000000;
    --white: #ffffff;
    --silver-top: #ffffff;
    --silver-mid: #c9c9cc;
    --silver-low: #8a8a90;
    --gold-light: #f2dcb8;
    --gold: #d8b88a;
    --gold-dark: #a8845a;
    --magenta: #d6309a;
    --orange: #f39a1e;
    --rule: #9a9a9a;
    --fire-deep: #3a1205;
    --fire-mid: #b8461a;
    --fire-glow: #f2b04a;
    --skin-glow: #e8c690;
  }
  * { margin: 0; padding: 0; box-sizing: border-box; }
  html, body { width: 893px; height: 1200px; overflow: hidden; background: var(--ink); }
  .flyer {
    position: relative;
    width: 893px;
    height: 1200px;
    background: var(--ink);
    overflow: hidden;
    font-family: "Roboto Condensed", "Arial Narrow", sans-serif;
    color: var(--white);
  }
  .hero-photo {
    position: absolute;
    left: 0; top: 200px;
    width: 893px; height: 600px;
    background:
      radial-gradient(ellipse 34% 46% at 78% 50%, var(--skin-glow) 0%, rgba(232,198,144,0.55) 45%, rgba(0,0,0,0) 100%),
      radial-gradient(ellipse 40% 30% at 55% 30%, var(--fire-glow) 0%, rgba(242,176,74,0.4) 40%, rgba(0,0,0,0) 100%),
      radial-gradient(ellipse 55% 35% at 35% 45%, var(--fire-mid) 0%, rgba(184,70,26,0.35) 50%, rgba(0,0,0,0) 100%),
      radial-gradient(ellipse 60% 45% at 30% 50%, var(--fire-deep) 0%, rgba(0,0,0,0) 100%);
  }
  .title-main {
    position: absolute;
    left: 0; right: 0; top: 40px;
    text-align: center;
    font-family: "Montserrat", sans-serif;
    font-weight: 800;
    font-size: 118px;
    letter-spacing: 1px;
    line-height: 1.1;
    background: linear-gradient(180deg, var(--silver-top) 0%, var(--silver-mid) 55%, var(--silver-low) 100%);
    -webkit-background-clip: text;
    background-clip: text;
    color: transparent;
  }
  .title-sub {
    position: absolute;
    left: 50px; top: 182px;
    font-family: "Montserrat", sans-serif;
    font-weight: 700;
    font-size: 58px;
    letter-spacing: 1px;
    line-height: 1.1;
    background: linear-gradient(180deg, var(--gold-light) 0%, var(--gold) 50%, var(--gold-dark) 100%);
    -webkit-background-clip: text;
    background-clip: text;
    color: transparent;
  }
  .presenter {
    position: absolute;
    left: 0; right: 0; top: 808px;
    text-align: center;
    font-family: "Montserrat", sans-serif;
    font-weight: 500;
    font-size: 30px;
    letter-spacing: 1px;
  }
  .date-band {
    position: absolute;
    left: 0; right: 0; top: 850px;
    height: 68px;
  }
  .date-band .rule {
    position: absolute;
    left: 250px; width: 393px; height: 1px;
    background: linear-gradient(90deg, rgba(154,154,154,0), var(--rule) 20%, var(--rule) 80%, rgba(154,154,154,0));
  }
  .date-band .rule.top { top: 0; }
  .date-band .rule.bottom { bottom: 0; }
  .date {
    position: absolute;
    left: 0; right: 0; top: 12px;
    text-align: center;
    font-family: "Montserrat", sans-serif;
    font-weight: 500;
    font-size: 40px;
    color: var(--magenta);
    letter-spacing: 1px;
  }
  .flourish {
    position: absolute;
    top: 8px;
    width: 130px; height: 52px;
    background: radial-gradient(ellipse at center, rgba(216,184,138,0.55) 0%, rgba(216,184,138,0) 70%);
  }
  .flourish.left { left: 80px; }
  .flourish.right { right: 50px; }
  .age-note {
    position: absolute;
    left: 0; right: 0; top: 935px;
    text-align: center;
    font-size: 28px;
    white-space: nowrap;
  }
  .age-note .sep { margin: 0 12px; }
  .divider {
    position: absolute;
    height: 1px;
    background: var(--rule);
  }
  .divider.short { left: 200px; width: 493px; top: 980px; }
  .divider.long { left: 130px; width: 636px; top: 1054px; }
  .headline-info {
    position: absolute;
    left: 0; right: 0; top: 992px;
    text-align: center;
    font-size: 44px;
    white-space: nowrap;
  }
  .headline-info .dj { color: var(--magenta); }
  .headline-info .sep { margin: 0 18px; }
  .details {
    position: absolute;
    left: 0; right: 0;
    text-align: center;
    font-size: 21px;
    white-space: nowrap;
  }
  .details.cost { top: 1068px; }
  .details.dress { top: 1100px; }
  .label { color: var(--magenta); }
  .tickets {
    position: absolute;
    left: 0; right: 0; top: 1136px;
    text-align: center;
    font-size: 28px;
    white-space: nowrap;
  }
  .tickets .phone { color: var(--orange); }
  .tickets .sep { margin: 0 12px; }
</style>
</head>
<body>
  <main class="flyer">
    <div class="hero-photo" role="img" aria-label="Photo of a laughing woman wearing headphones, her hair streaming into flames and smoke"></div>

    <h1 class="title-main">MOONLIT</h1>
    <p class="title-sub">GLOW PARTY</p>

    <p class="presenter">QVN EVENTS PRESENTS</p>

    <div class="date-band">
      <div class="rule top"></div>
      <div class="flourish left" role="img" aria-label="Gold ornamental flourish"></div>
      <p class="date">NOVEMBER 2013</p>
      <div class="flourish right" role="img" aria-label="Gold ornamental flourish"></div>
      <div class="rule bottom"></div>
    </div>

    <p class="age-note">DOORS OPEN 8PM<span class="sep">|</span>ENTRY STRICTLY OVER 18'S.</p>
    <div class="divider short"></div>

    <p class="headline-info"><span class="dj">DJ COPPER WHISK</span><span class="sep">|</span><span class="venue">VENUE: TBA</span></p>
    <div class="divider long"></div>

    <p class="details cost"><span class="label">COST:</span> $60 PER HEAD &nbsp;|&nbsp; INCLUDES CHAMPAGNE, &nbsp;BEER &amp; WINE AND CANAPES.</p>
    <p class="details dress"><span class="label">DRESS CODE:</span> &nbsp;SMART CASUAL SULTRY SEXY SPRING THREADS</p>

    <p class="tickets"><span class="label">Tickets from:</span> www.quillvanenest.example.com.au<span class="sep">|</span><span class="phone">0499 371 582</span></p>
  </main>
</body>
</html>
```